Manuka Honey company needs a Upmarket, Luxury Website!

New Zealand, Taranaki based Manuka Honey company Rimu Vale Honey is looking for a new website, we are looking for an upmarket, luxury, serious website design. We export the highest quality quality Manuka Honey, straight from the Taranaki region.

Main export markets are Asia & Europe, also New Zealand & Australia.

Looking to have a beautiful, upmarket, serious, luxurious & graphical experience with mobile optimization in mind. Like the use of product staging/mockups

You can use copy from other websites to build the site and we will change the copy after the design is finished.

***Please include 'Honey Product' mockups in website.

*Will add illustrator files in coming days***

Feel free to make website functional in Shopify, Wordpress or WIX

Target Market(s)

Asia, Europe (main markets) New Zealand, Australia (Submarkets)

Coding

Coded - Design and coding required

Number of Pages Required

4 page

Requirements
Must have
• Home, Shop, About Us, Contact Us

Homepage to include:

Our Products
Company Video (video under construction)
What is MGO/KPS
Newsletter Opt-in

***(Not in Order)***

Please include 'Honey Product' mockups in website.
*Will add illustrator files in coming days
Nice to have
• FAQ & Partnership Inquiries (hyperlink in footer)

```html
<!DOCTYPE html>
<html lang="en">
<head>
<meta charset="utf-8">
<title>Rimu Vale Honey — Manuka Honey</title>
<link href="https://fonts.googleapis.com/css2?family=Montserrat:wght@400;500;600;700;800&display=swap" rel="stylesheet">
<style>
:root{
  --amber:#f9b000;
  --gold:#c99a06;
  --gold-text:#c8920a;
  --ink:#141414;
  --body:#555;
  --muted:#777;
  --cream:#f5f2ee;
  --comb:#f7ecd8;
  --footer:#2b2b2b;
  --white:#fff;
}
*{margin:0;padding:0;box-sizing:border-box}
html,body{width:1200px;height:4011px;overflow:hidden}
body{position:relative;font-family:"Montserrat",sans-serif;color:var(--ink);background:var(--white)}
.abs{position:absolute}
a{color:inherit;text-decoration:none}

/* header */
.brand{left:84px;top:58px;display:flex;align-items:center;gap:12px;z-index:2}
.brand-dot{width:40px;height:40px;border-radius:50%;background:var(--amber)}
.brand-name{font-size:22px;font-weight:500;letter-spacing:3px;color:var(--ink)}
.nav{left:549px;top:66px;display:flex;gap:30px;font-size:11px;font-weight:500;color:#333;z-index:2}
.nav .active{color:var(--amber)}
.cart{left:956px;top:61px;z-index:2}
.btn-small{left:1023px;top:60px;width:84px;height:24px;background:var(--amber);color:var(--ink);font-size:9px;font-weight:700;display:flex;align-items:center;justify-content:center;border-radius:2px;z-index:2}

/* hero */
.hero{left:0;top:0;width:1200px;height:731px;background:linear-gradient(90deg,#f9e7b6 0%,#fdf6e4 22%,#fff 42%)}
.hero-visual{left:680px;top:218px;width:470px;height:460px;border-radius:50% 45% 40% 50%;background:radial-gradient(ellipse at 45% 45%,#f2a81a 0%,#e8b45a 35%,#f6dfae 60%,rgba(255,255,255,0) 75%);z-index:0}
.hero-kicker{left:92px;top:321px;font-size:13px;font-weight:600;color:var(--amber);z-index:2}
.hero-title{left:90px;top:332px;font-size:62px;font-weight:800;letter-spacing:1px;white-space:nowrap;z-index:2}
.hero-text{left:92px;top:420px;width:510px;font-size:13.5px;line-height:1.3;color:#444;z-index:2}
.hero-btn{left:92px;top:521px;width:128px;height:41px;background:var(--amber);font-size:12px;font-weight:700;display:flex;align-items:center;justify-content:center;border-radius:2px;z-index:2}
.hero-arrow{left:42px;top:534px;z-index:2}

/* about */
.about{left:0;top:731px;width:1200px;height:467px;background:var(--amber)}
.about-photo{left:87px;top:804px;width:487px;height:324px;background:linear-gradient(120deg,#d07a14 0%,#e8b86a 40%,#f3d5d8 70%,#efe3ee 100%)}
.about-kicker{left:638px;top:822px;font-size:10px;font-weight:600;letter-spacing:1px;color:var(--white)}
.about-title{left:636px;top:836px;font-size:34px;font-weight:700;color:var(--ink);white-space:nowrap}
.about-line{left:648px;top:890px}
.about-copy{left:647px;top:947px;width:418px;font-size:12px;line-height:1.35;color:#3a2a00;text-align:justify}
.about-copy p{margin-bottom:16px}

/* products */
.products{left:5px;top:1198px;width:1190px;height:790px;background:var(--cream)}
.section-title{width:1200px;left:0;text-align:center;font-weight:700}
.products-title{top:1300px;font-size:37px}
.products-title span{color:var(--gold-text)}
.squiggle{left:505px;top:1357px}
.arrow-side{top:1535px}
.product{top:1431px;width:300px;text-align:center}
.product-shot{width:210px;height:190px;margin:0 auto;border-radius:30px}
.product h3{margin-top:38px;font-size:16px;font-weight:600;letter-spacing:.3px}
.product .price{margin-top:5px;font-size:17px;font-weight:700;color:var(--gold-text)}
.product p{margin:12px auto 0;width:280px;font-size:10px;line-height:1.35;color:var(--muted)}
.product .add{margin-top:18px;font-size:9px;font-weight:700;display:flex;justify-content:center;align-items:center;gap:8px}
.btn-view{left:535px;top:1830px;width:136px;height:36px;background:var(--gold);color:var(--white);font-size:11px;font-weight:700;display:flex;align-items:center;justify-content:center}

/* newsletter */
.news-visual{left:70px;top:2069px;width:503px;height:249px;border-radius:50%;background:radial-gradient(ellipse at 55% 50%,#f0a320 0%,#f5c45c 40%,#fbe8b4 65%,rgba(255,255,255,0) 80%)}
.news-dot{left:614px;top:2059px;width:46px;height:46px;border-radius:50%;background:#e9ecf2}
.news-title{left:676px;top:2063px;font-size:30px;font-weight:700;color:var(--gold-text);white-space:nowrap}
.news-rule{left:621px;top:2119px;width:86px;height:3px;background:var(--gold)}
.news-copy{left:621px;top:2147px;width:486px;font-size:11.5px;font-weight:500;line-height:1.33;color:#333;text-align:justify}
.news-input{left:619px;top:2270px;width:335px;height:48px;border:2px solid #444;font-size:13px;padding:0 18px;display:flex;align-items:center;color:#222}
.news-btn{left:960px;top:2270px;width:145px;height:48px;background:var(--gold);color:var(--white);font-size:13px;font-weight:700;display:flex;align-items:center;justify-content:center}

/* blog */
.blog{left:0;top:2423px;width:1200px;height:774px;background:var(--comb)}
.head-dot{width:40px;height:40px;border-radius:50%;background:#e9ecf2}
.blog-head{left:0;top:2486px;width:1200px;display:flex;justify-content:center;align-items:center;gap:6px}
.blog-head h2{font-size:31px;font-weight:600;color:var(--gold-text)}
.blog-sub{left:370px;top:2557px;width:460px;text-align:center;font-size:12px;line-height:1.4;color:var(--muted)}
.card{top:2647px;width:311px;height:434px;background:var(--white)}
.card-photo{height:205px}
.card-body{padding:22px 18px 0 18px}
.card-meta{font-size:10px;font-weight:600;color:#222}
.card h3{margin-top:12px;font-size:17px;font-weight:600;line-height:1.22;color:var(--gold-text)}
.card p{margin-top:14px;font-size:10.5px;line-height:1.42;color:var(--muted)}
.card .btn-read{margin-top:18px;width:124px;height:30px;border-radius:15px;background:var(--gold);color:var(--white);font-size:10px;font-weight:700;display:flex;align-items:center;justify-content:center}

/* testimonials */
.testi-head{left:0;top:3292px;width:1200px;display:flex;justify-content:center;align-items:center;gap:14px}
.testi-head h2{font-size:30px;font-weight:600;color:var(--gold-text)}
.quote{top:3397px;width:314px;height:132px;border:2px solid #888;padding:30px 22px 0 22px;background:var(--white)}
.quote .mark{position:absolute;left:22px;top:-8px;font-size:38px;font-weight:800;color:var(--gold-text);line-height:1;background:var(--white);padding:0 3px}
.quote h4{font-size:12.5px;font-weight:600;color:var(--gold-text)}
.quote p{margin-top:5px;font-size:11px;line-height:1.38;color:var(--muted)}
.quote .tail{position:absolute;left:26px;bottom:-9px;width:14px;height:14px;background:var(--white);border-right:2px solid #888;border-bottom:2px solid #888;transform:rotate(45deg)}
.person{top:3546px;font-size:13px;font-weight:700;color:var(--gold-text)}
.person span{display:block;font-size:11px;font-weight:500;color:#333}
.pager{top:3451px;width:22px;height:22px;background:#555;display:flex;align-items:center;justify-content:center}

/* footer */
.footer{left:0;top:3664px;width:1200px;height:301px;background:var(--footer);color:#ddd}
.foot-brand{left:89px;top:3722px;display:flex;align-items:center;gap:10px}
.foot-brand .brand-dot{width:32px;height:32px}
.foot-brand .brand-name{font-size:16px;color:#eee;letter-spacing:2.5px}
.foot-about{left:89px;top:3786px;width:210px;font-size:12px;line-height:1.35;color:#eee;text-align:justify}
.foot-head{top:3728px;font-size:17px;font-weight:700;color:var(--gold-text);text-decoration:underline;text-underline-offset:4px}
.foot-links{left:402px;top:3773px;list-style:none;font-size:13px;color:#eee}
.foot-links li{margin-bottom:8px;display:flex;align-items:center;gap:10px}
.foot-links li::before{content:"";width:5px;height:5px;border-radius:50%;background:var(--amber)}
.foot-contact{left:626px;top:3773px;font-size:12px;line-height:1.4;color:#eee}
.foot-contact .gap{height:16px}
.socials{left:627px;top:3892px;display:flex;gap:9px}
.socials span{width:17px;height:17px;border-radius:50%;background:var(--gold)}
.gallery{left:887px;top:3773px;display:grid;grid-template-columns:repeat(3,70px);gap:6px}
.gallery div{height:70px;border:2px solid #fff}
.bottom-bar{left:0;top:3965px;width:1200px;height:46px;background:var(--gold);color:#fff;font-size:12px;display:flex;align-items:center;justify-content:center}
</style>
</head>
<body>

<!-- Header -->
<div class="hero abs"></div>
<div class="hero-visual abs" role="img" aria-label="Jar of manuka honey with a wooden spoon, honeycomb and flowering manuka sprig"></div>
<div class="brand abs"><span class="brand-dot"></span><span class="brand-name">RIMU VALE HONEY</span></div>
<nav class="nav abs">
  <a class="active" href="#">Home</a><a href="#">Shop</a><a href="#">About Us</a><a href="#">Products</a><a href="#">Blog</a><a href="#">Contact Us</a>
</nav>
<svg class="cart abs" width="26" height="22" viewBox="0 0 26 22" aria-hidden="true">
  <path d="M1 2h4l3 12h12l3-9H7" fill="none" stroke="#d99c06" stroke-width="2"/>
  <circle cx="10" cy="18" r="2" fill="#d99c06"/><circle cx="19" cy="18" r="2" fill="#d99c06"/>
  <circle cx="22" cy="3" r="3" fill="#3aa7d8"/>
</svg>
<a class="btn-small abs" href="#">SHOP NOW</a>

<!-- Hero -->
<div class="hero-kicker abs">WELCOME TO RIMU VALE HONEY CO</div>
<h1 class="hero-title abs">MANUKA HONEY</h1>
<p class="hero-text abs">Nam quibus rebus efficiuntur voluptates, eae non sunt in potestate sapientis. Negare non possum. Huic mori optimum esse propter desperationem sapientiae, illi propter spem vivere. Quid enim me prohiberet</p>
<a class="hero-btn abs" href="#">SHOP NOW</a>
<svg class="hero-arrow abs" width="16" height="36" viewBox="0 0 16 36" aria-hidden="true"><path d="M14 2L2 18l12 16" fill="none" stroke="#fff" stroke-width="2"/></svg>

<!-- About -->
<section class="about abs"></section>
<div class="about-photo abs" role="img" aria-label="Bowl of honey with a honey dipper beside manuka blossoms on a pink cloth"></div>
<div class="about-kicker abs">ABOUT US</div>
<h2 class="about-title abs">Welcome to Rimu Vale Honey</h2>
<svg class="about-line abs" width="140" height="26" viewBox="0 0 140 26" aria-hidden="true"><path d="M2 22 C30 4 60 20 90 14 S125 10 132 12" fill="none" stroke="#3a2a00" stroke-width="1.3" stroke-dasharray="3 3"/><circle cx="133" cy="11" r="4" fill="#3a2a00"/></svg>
<div class="about-copy abs">
  <p>constructio interrete. Quia nec honesto quic quam honestius nec turpi turpius. Tria genera bonorum; Quid iudicant sensus? Quae qui non vident, nihil umquam magnum ac cognitione</p>
  <p>dignum amaverunt. Dicet pro me ipsa virtus nec dubitabit isti vestro beato M. Nihil ad rem! Ne sit sane; Nihil ad rem! Ne sit sane; Philosophi autem in suis lectulis plerumque</p>
  <p>moriuntur. Paulum, cum regem Persem captum adduceret, eodem flumine invectio?</p>
</div>

<!-- Products -->
<section class="products abs"></section>
<h2 class="section-title products-title abs"><span>OUR</span> PRODUCTS</h2>
<svg class="squiggle abs" width="140" height="26" viewBox="0 0 140 26" aria-hidden="true"><path d="M2 14 C30 4 60 22 90 16 S125 10 132 10" fill="none" stroke="#222" stroke-width="1.3" stroke-dasharray="3 3"/><circle cx="133" cy="9" r="4" fill="#222"/></svg>
<svg class="arrow-side abs" style="left:52px" width="18" height="36" viewBox="0 0 18 36" aria-hidden="true"><path d="M16 2L2 18l14 16" fill="none" stroke="#c8920a" stroke-width="2"/></svg>
<svg class="arrow-side abs" style="left:1138px" width="18" height="36" viewBox="0 0 18 36" aria-hidden="true"><path d="M2 2l14 16L2 34" fill="none" stroke="#c8920a" stroke-width="2"/></svg>

<div class="product abs" style="left:117px">
  <div class="product-shot" role="img" aria-label="Golden honeycomb pieces" style="background:radial-gradient(circle,#f3a517 0%,#f6c766 55%,rgba(245,242,238,0) 75%)"></div>
  <h3>SUMMUM&nbsp; VAOBIS</h3><div class="price">$250.00</div>
  <p>Lorem ipsum dolor sit amet, cu per porro dolore nostro, partem integre corpora per ea, tation</p>
  <div class="add"><svg width="12" height="10" viewBox="0 0 12 10"><path d="M0 1h2l2 6h6l2-5H3" fill="none" stroke="#d99c06" stroke-width="1.5"/></svg>ADD TO CARD</div>
</div>
<div class="product abs" style="left:454px">
  <div class="product-shot" role="img" aria-label="Jar of honey with a burlap lid cover" style="background:radial-gradient(ellipse at 50% 55%,#f0b400 0%,#f4cc55 45%,#c9a87a 60%,rgba(245,242,238,0) 75%)"></div>
  <h3>BONUM VOLUPTAS</h3><div class="price">$548.00</div>
  <p>ornatus mel ad. Brute voluptatibus an est, per que torquatos, ei eam amet hinc. Ne vix tio</p>
  <div class="add"><svg width="12" height="10" viewBox="0 0 12 10"><path d="M0 1h2l2 6h6l2-5H3" fill="none" stroke="#d99c06" stroke-width="1.5"/></svg>ADD TO CARD</div>
</div>
<div class="product abs" style="left:805px">
  <div class="product-shot" role="img" aria-label="Small round jar of honey with a burlap lid cover" style="background:radial-gradient(ellipse at 50% 58%,#ef9a00 0%,#f5bb3a 40%,#c9a87a 58%,rgba(245,242,238,0) 72%)"></div>
  <h3>DEMOCRITEUM PUTO</h3><div class="price">$250.00</div>
  <p>insolens, eos ei nostrud appellantur, an autem dolorem vel. Ne adhuc accusata eleifend v</p>
  <div class="add"><svg width="12" height="10" viewBox="0 0 12 10"><path d="M0 1h2l2 6h6l2-5H3" fill="none" stroke="#d99c06" stroke-width="1.5"/></svg>ADD TO CARD</div>
</div>
<a class="btn-view abs" href="#">VIEW MORE</a>

<!-- Newsletter -->
<div class="news-visual abs" role="img" aria-label="Piece of honeycomb resting in a pool of honey"></div>
<span class="news-dot abs"></span>
<h2 class="news-title abs">NEWSLETTER SIGN UP</h2>
<div class="news-rule abs"></div>
<p class="news-copy abs">constructio interrete. Quia nec honesto quic quam honestius nec turpi turpius. Tria genera bonorum; Quid iudicant sensus? Quae qui non vident, nihil umquam magnum ac cognitione dignum amaverunt. Dicet pro me ipsa virtus nec dubitabit isti vestro beato M. Nihil ad rem! Ne sit saneNe sit sane; Nihil ad rem! Ne sit sane; Philosophi autem in suis lectulis plerumque moriuntur. Paulum, cum regem</p>
<div class="news-input abs">Email Address</div>
<a class="news-btn abs" href="#">SUBSCRIBE</a>

<!-- Blog -->
<section class="blog abs"></section>
<div class="blog-head abs"><span class="head-dot"></span><h2>Lates Blog</h2></div>
<p class="blog-sub abs">Lorem ipsum dolor sit amet, cu per porro dolore nostro, partem cu per porro integre corpora per ea, tation ornatus mel ad</p>

<article class="card abs" style="left:107px">
  <div class="card-photo" role="img" aria-label="Beekeepers tending hives in an orchard" style="background:linear-gradient(180deg,#8fb55a 0%,#6d8f3c 50%,#c98a3a 100%)"></div>
  <div class="card-body">
    <div class="card-meta">By Admin | 4 January 2021</div>
    <h3>Lorem ipsum dolor sit amet cu per porro dolore nostro</h3>
    <p>Lorem ipsum dolor sit amet, cu per porro dolore nostro, partem integre corpora per ea, tation ornatus mel ad Brute voluptatibus an</p>
    <a class="btn-read" href="#">READ MORE</a>
  </div>
</article>
<article class="card abs" style="left:442px">
  <div class="card-photo" role="img" aria-label="Honey dripping from a dipper into a glass bowl among yellow flowers" style="background:linear-gradient(120deg,#7e9b2c 0%,#d7c23a 45%,#f1d54a 70%,#eee7d8 100%)"></div>
  <div class="card-body">
    <div class="card-meta">By Admin | 4 January 2021</div>
    <h3>Sum dolor sit amet cu per porro dolore nostro</h3>
    <p>Lorem ipsum dolor sit amet, cu per porro dolore nostro, partem integre corpora per ea, tation ornatus mel ad Brute voluptatibus an</p>
    <a class="btn-read" href="#">READ MORE</a>
  </div>
</article>
<article class="card abs" style="left:778px">
  <div class="card-photo" role="img" aria-label="Bees working on golden honeycomb" style="background:linear-gradient(160deg,#a0611a 0%,#e59c2c 50%,#f3c466 100%)"></div>
  <div class="card-body">
    <div class="card-meta">By Admin | 4 January 2021</div>
    <h3>Porro dolore nostro Lorem ipsum dolor sit ametcu per</h3>
    <p>Lorem ipsum dolor sit amet, cu per porro dolore nostro, partem integre corpora per ea, tation ornatus mel ad Brute voluptatibus an</p>
    <a class="btn-read" href="#">READ MORE</a>
  </div>
</article>

<!-- Testimonials -->
<div class="testi-head abs"><span class="head-dot"></span><h2>Testimonials</h2></div>
<div class="pager abs" style="left:184px"><svg width="8" height="10" viewBox="0 0 8 10"><path d="M6 1L2 5l4 4" fill="none" stroke="#fff" stroke-width="1.5"/></svg></div>
<div class="pager abs" style="left:996px"><svg width="8" height="10" viewBox="0 0 8 10"><path d="M2 1l4 4-4 4" fill="none" stroke="#fff" stroke-width="1.5"/></svg></div>

<div class="quote abs" style="left:257px">
  <span class="mark">“</span>
  <h4>Highly Professional Team</h4>
  <p>Lorem ipsum dolor sit amet, consectetur adipiscing elit. Quid autem habent admirationis, cum prope accesseris? An hoc usque quaque, aliter in vita?</p>
  <span class="tail"></span>
</div>
<div class="person abs" style="left:289px">TAMATI<span>Manager</span></div>

<div class="quote abs" style="left:632px">
  <span class="mark">“</span>
  <h4>Highly Professional Team</h4>
  <p>Lorem ipsum dolor sit amet, consectetur adipiscing elit. Quid autem habent admirationis, cum prope accesseris? An hoc usque quaque, aliter in vita?</p>
  <span class="tail"></span>
</div>
<div class="person abs" style="left:667px">MEREANA HOLLIS<span>Top Manager</span></div>

<!-- Footer -->
<footer class="footer abs"></footer>
<div class="foot-brand abs"><span class="brand-dot"></span><span class="brand-name">RIMU VALE HONEY</span></div>
<p class="foot-about abs">quaerimus, qualis Q. Nam quibus rebus efficiuntur voluptates, eae non sunt in potestate sapientis. Negare non possum. Huic mori optimum esse propter desperationem sapientiae, illi propter spem vivere. Quid prohiberetfalsone,se privasse</p>

<div class="foot-head abs" style="left:398px">QUICK LINK</div>
<ul class="foot-links abs">
  <li>Home</li><li>Shop</li><li>About Us</li><li>Products</li><li>Blog</li><li>Contact Us</li>
</ul>

<div class="foot-head abs" style="left:626px">CONTACT US</div>
<div class="foot-contact abs">
  14 Kowhai Road<br>Stratford, Taranaki 4332
  <div class="gap"></div>
  06-555-0142<br>hello@rimuvalehoney.co<br>www.rimuvalehoney.co
</div>
<div class="socials abs"><span></span><span></span><span></span><span></span></div>

<div class="foot-head abs" style="left:887px">PHOTOGALLERY</div>
<div class="gallery abs" role="img" aria-label="Gallery of honey jars, honeycomb and honey dippers">
  <div style="background:linear-gradient(#f1e2bf,#e6a51c)"></div>
  <div style="background:linear-gradient(#f7c35a,#e48a12)"></div>
  <div style="background:linear-gradient(#fbeed0,#d9801a)"></div>
  <div style="background:linear-gradient(#8a5a1e,#f0a820)"></div>
  <div style="background:linear-gradient(#f4d7a3,#e59a2c)"></div>
  <div style="background:linear-gradient(#f8ebcf,#f3c24a)"></div>
</div>

<div class="bottom-bar abs">Copyright 2020, Kereru Studio, All Right Reserved</div>

</body>
</html>
```